Prime Global Casting Agency Needs creative business card design

We manage actors careers and book them liaising and promoting their profiles internationally through Casting Directors, Producers, Directors, Publicists etc. We need clearly visable contact details but with a design that reflects our status and creativity of TV, Feature Film industry. Our logo is attached and needs to relate and our website is www.brisklanestagefolk.com
No flame designs please but please incorporate logo colours.

Target Market(s)

Clients

Industry/Entity Type

Film Production

Contact Information for Business Card

Director Danielle Prowse
Suite F, Building 4, Wrenlow Studios Australia, Kelby Vale, Sydney, NSW 2048

Font styles to use
Sans Serif

Colors
ec1f27

Requirements
Nice to have
• Colours should relate to logo attached and type can relate again to type in the logo design.
Should not have
• No Flames designs and best to be not too obvious with the film designs eiither. Needs to be more creative and modern

```html
<!DOCTYPE html>
<html lang="en">
<head>
<meta charset="utf-8">
<title>Brisklane Stagefolk – Business Card</title>
<link href="https://fonts.googleapis.com/css2?family=Lato:wght@400;700&display=swap" rel="stylesheet">
<style>
  :root {
    --brand-red: #ec1f27;
    --ink: #2a2a2a;
    --card: #f7f7f7;
    --backdrop: #e9e9e9;
    --card-edge: #dcdcdc;
  }
  * { margin: 0; padding: 0; box-sizing: border-box; }
  html, body {
    width: 1200px; height: 900px; overflow: hidden;
    background: var(--backdrop);
    font-family: "Lato", Arial, sans-serif;
  }
  .stage {
    position: relative; width: 1200px; height: 900px;
    display: flex; align-items: center; justify-content: center; gap: 40px;
  }
  .card {
    position: relative; width: 520px; height: 297px;
    background: var(--card);
    border: 1px solid var(--card-edge);
    box-shadow: 0 6px 18px rgba(0,0,0,0.08);
  }
  .contact-card .person {
    position: absolute; left: 36px; top: 34px;
  }
  .person-name {
    color: var(--brand-red); font-weight: 700; font-size: 22px; line-height: 1.1;
  }
  .person-role {
    color: var(--ink); font-size: 13px; margin-top: 3px;
  }
  .contact-list {
    position: absolute; left: 36px; top: 118px; list-style: none;
  }
  .contact-list li { margin-bottom: 6px; }
  .contact-label {
    display: block; color: var(--brand-red); font-size: 12px; line-height: 1.2;
  }
  .contact-value {
    display: block; color: var(--ink); font-size: 14px; line-height: 1.25;
  }
  .brand {
    position: absolute; display: flex; align-items: center; gap: 10px;
  }
  .brand-mark {
    width: 14px; height: 14px; background: var(--brand-red);
  }
  .brand-name {
    color: var(--brand-red); font-weight: 700; white-space: nowrap;
  }
  .contact-card .brand { right: 34px; top: 150px; }
  .contact-card .brand-name { font-size: 22px; }
  .logo-card .brand {
    left: 50%; top: 50%; transform: translate(-50%, -50%);
  }
  .logo-card .brand-mark { width: 20px; height: 20px; }
  .logo-card .brand-name { font-size: 34px; }
</style>
</head>
<body>
  <main class="stage">
    <section class="card contact-card">
      <div class="person">
        <p class="person-name">Owen Ratcliffe</p>
        <p class="person-role">Managing Director</p>
      </div>
      <ul class="contact-list">
        <li><span class="contact-label">telephone</span><span class="contact-value">044-555 018 274</span></li>
        <li><span class="contact-label">email</span><span class="contact-value">info@brisklane.com</span></li>
        <li><span class="contact-label">address</span><span class="contact-value">2345, adress goes here, country</span></li>
      </ul>
      <div class="brand">
        <span class="brand-mark"></span>
        <span class="brand-name">Brisklane Stagefolk</span>
      </div>
    </section>
    <section class="card logo-card">
      <div class="brand">
        <span class="brand-mark"></span>
        <span class="brand-name">Brisklane Stagefolk</span>
      </div>
    </section>
  </main>
</body>
</html>
```